Keystone Trench Co Business Card*

Looking for a professional, clean and crisp business card

I am in the underground utilities industry and am just looking for a really impressive business card. I would like our card to be white with our symbol crisp and clear with it protruding. I also have a business partner that will require his name and info on the card once the design is set. I would like to have our website info on the card which is;
http://keystonetrenchco.example/

Contact Information for Business Card

Website, contact name, number and email

```html
<!DOCTYPE html>
<html lang="en">
<head>
<meta charset="utf-8">
<title>Keystone Trench Co Business Card</title>
<link href="https://fonts.googleapis.com/css2?family=Poppins:wght@400;500;700&display=swap" rel="stylesheet">
<style>
  :root {
    --page-bg: #e6e6e6;
    --card-white: #ffffff;
    --card-dark: #1f1f1f;
    --brand-blue: #3a5fa8;
    --accent-red: #e3262b;
    --ink: #222222;
    --text-gray: #555555;
    --rule-gray: #7a7a7a;
  }
  * { margin: 0; padding: 0; box-sizing: border-box; }
  html, body {
    width: 1125px;
    height: 1200px;
    overflow: hidden;
    background: var(--page-bg);
    font-family: "Poppins", sans-serif;
  }
  .canvas { position: relative; width: 1125px; height: 1200px; }
  .card { position: absolute; overflow: hidden; }

  .card-front {
    left: 153px; top: 106px; width: 825px; height: 470px;
    background: var(--card-white);
  }
  .brand-lockup {
    position: absolute;
    left: 224px; top: 237px;
    transform: translate(-50%, -50%);
    display: flex; align-items: center; gap: 12px;
    white-space: nowrap;
  }
  .brand-mark {
    width: 18px; height: 18px; border-radius: 50%;
    background: var(--ink);
  }
  .brand-name {
    font-weight: 700; font-size: 24px; color: var(--ink);
    letter-spacing: 0.5px;
  }
  .divider {
    position: absolute; left: 373px; top: 134px;
    width: 1px; height: 203px; background: var(--rule-gray);
  }
  .contact {
    position: absolute; left: 412px; top: 126px;
    color: var(--text-gray); font-size: 18.5px; line-height: 23px;
  }
  .contact-name {
    font-weight: 500; font-size: 26px; line-height: 34px;
    color: var(--brand-blue); letter-spacing: 0.3px;
  }
  .contact-role { color: var(--accent-red); font-size: 18px; line-height: 24px; }
  .contact-address { margin-top: 16px; }
  .contact-lines { margin-top: 18px; }
  .base-band {
    position: absolute; left: 0; bottom: 0;
    width: 100%; height: 14px; background: var(--brand-blue);
  }

  .card-back {
    left: 143px; top: 633px; width: 845px; height: 482px;
    background: var(--card-dark);
    display: flex; align-items: center; justify-content: center;
  }
  .back-lockup { display: flex; align-items: center; gap: 18px; }
  .back-mark {
    width: 26px; height: 26px; border-radius: 50%;
    background: var(--card-white);
  }
  .back-name {
    font-weight: 700; font-size: 44px; color: var(--card-white);
    letter-spacing: 1px;
  }
</style>
</head>
<body>
<main class="canvas">
  <section class="card card-front" aria-label="Business card front">
    <div class="brand-lockup">
      <span class="brand-mark"></span>
      <span class="brand-name">Keystone Trench Co</span>
    </div>
    <div class="divider"></div>
    <div class="contact">
      <p class="contact-name">DANIEL HARTWELL</p>
      <p class="contact-role">President</p>
      <p class="contact-address">4120 Birchwood Court<br>Fairbanks, Alaska 99701</p>
      <p class="contact-lines">P. 555-014-2287<br>info@keystonetrenchco.example<br>www.keystonetrenchco.example</p>
    </div>
    <div class="base-band"></div>
  </section>

  <section class="card card-back" aria-label="Business card back">
    <div class="back-lockup">
      <span class="back-mark"></span>
      <span class="back-name">Keystone Trench Co</span>
    </div>
  </section>
</main>
</body>
</html>
```